Forensic Document Examiner, looking for contemporary update to my stationery design.

Looking for professional, classy logo design for stationery and business cards. My current stationery and business card is attached.I believe a logo image makes a header section interesting, so an intriguing design of a pen, feathered pen, microscope, magnifying glass, etc., would be appropriate. I have been in the business for over 30 years. I leave ideas to the imagination of the designer.My work involves mainly, the comparison of signatures and handwriting. I also resolve alterations, obliterations, and work as shown on my website: www.documentexaminer.infoThe image produced will be printed on quality white stationery and envelopes. The stationery will be photocopied by my clients, so the images should be reproducible. The business cards may be designed in other than white.

Target Market(s)

Attorneys

Font styles to use
Sans Serif

Colors

Designer to choose colors to be used in the design.

Requirements
Must have
• Image suitable for white stationery and photocopying.
• Classy logo and image; no casual fonts.
Nice to have
• Intriguing, contemporary design incorporating a relevant logo to my work.

```html
<!DOCTYPE html>
<html lang="en">
<head>
<meta charset="utf-8">
<title>Daniel R.Moore – Key Tag Designs</title>
<link href="https://fonts.googleapis.com/css2?family=Crimson+Pro:ital,wght@0,600;1,400;1,600&family=Roboto+Condensed:wght@400&display=swap" rel="stylesheet">
<style>
  :root {
    --bg: #e4e4e6;
    --tag-white: #f4f4f6;
    --navy: #2a2566;
    --violet: #5a4bc0;
    --violet-deep: #352b8a;
    --grey-text: #77777d;
    --rule: #b9b9c0;
    --gold: #e2c12a;
    --icon-tone: #d3d3d8;
  }
  * { margin: 0; padding: 0; box-sizing: border-box; }
  html, body { width: 1200px; height: 1185px; overflow: hidden; }
  body { background: var(--bg); position: relative; font-family: "Crimson Pro", Georgia, serif; }

  .tag { position: absolute; overflow: hidden; background: var(--tag-white); box-shadow: 0 3px 10px rgba(0,0,0,.12); }
  .tag-oval { left: 330px; top: 170px; width: 460px; height: 330px; border-radius: 70px / 60px; }
  .tag-card { left: 300px; top: 630px; width: 600px; height: 360px; border-radius: 12px; }

  .mark-art { position: absolute; background: linear-gradient(160deg, var(--icon-tone), #bfc0c8); border-radius: 6px; }
  .tag-oval .mark-art { left: 62px; top: 42px; width: 80px; height: 118px; }
  .tag-card .mark-art { left: 70px; top: 120px; width: 100px; height: 145px; }
  .mark-base { position: absolute; height: 4px; background: var(--violet-deep); }

  .name { position: absolute; color: var(--navy); font-weight: 600; font-size: 40px; line-height: 1; white-space: nowrap; }
  .role { position: absolute; color: var(--grey-text); font-style: italic; font-size: 21px; letter-spacing: .5px; white-space: nowrap; }

  .rule { position: absolute; height: 1px; background: var(--rule); }
  .rule::before, .rule::after { content: ""; position: absolute; top: -1.5px; width: 4px; height: 4px; background: var(--gold); }
  .rule::before { left: 0; } .rule::after { right: 0; }

  .tagline { position: absolute; left: 16px; right: 16px; top: 198px; text-align: center; font-family: "Roboto Condensed", Arial, sans-serif; font-size: 15px; line-height: 1.35; color: var(--navy); }
  .tagline span { display: block; white-space: nowrap; }

  .band { position: absolute; left: 0; right: 0; bottom: 0; height: 62px; background: linear-gradient(90deg, var(--violet-deep), var(--violet)); }
  .url { position: absolute; font-style: italic; font-weight: 600; white-space: nowrap; }
  .tag-oval .url { left: 0; right: 0; bottom: 14px; text-align: center; color: #fff; font-size: 24px; }
  .tag-card .url { left: 145px; top: 300px; color: var(--navy); font-size: 22px; font-weight: 400; }

  .swoosh { position: absolute; inset: 0; }
</style>
</head>
<body>

  <section class="tag tag-oval">
    <div class="mark-art" role="img" aria-label="Microscope illustration in grey and violet"></div>
    <div class="mark-base" style="left:56px; top:166px; width:92px;"></div>
    <h1 class="name" style="left:170px; top:70px;">Daniel R.Moore</h1>
    <p class="role" style="left:176px; top:114px;">Forensic Document Examinar</p>
    <div class="rule" style="left:50px; right:50px; top:188px;"></div>
    <p class="tagline"><span>Full service laboratory specializing in handwriting comparisons,</span><span>obliterations, alterations, indented writing recovery etc.</span></p>
    <div class="band"></div>
    <p class="url">www.quillmarkreview.info</p>
  </section>

  <section class="tag tag-card">
    <svg class="swoosh" viewBox="0 0 600 360" preserveAspectRatio="none" aria-hidden="true">
      <defs>
        <linearGradient id="swooshFill" x1="0" y1="0" x2="1" y2="1">
          <stop offset="0" stop-color="#2e2676"/>
          <stop offset="1" stop-color="#5c4dc4"/>
        </linearGradient>
      </defs>
      <path d="M300 0 C460 30 560 180 520 360 L600 360 L600 0 Z" fill="url(#swooshFill)"/>
      <path d="M420 0 C540 60 600 200 560 360 L600 360 L600 0 Z" fill="#6a5bd0" opacity=".45"/>
    </svg>
    <div class="mark-art" role="img" aria-label="Microscope illustration in grey and violet"></div>
    <div class="mark-base" style="left:65px; top:272px; width:110px;"></div>
    <h1 class="name" style="left:190px; top:150px;">Daniel R.Moore</h1>
    <p class="role" style="left:196px; top:196px;">Forensic Document Examinar</p>
    <div class="rule" style="left:160px; width:310px; top:285px;"></div>
    <p class="url">www.quillmarkreview.info</p>
  </section>

</body>
</html>
```